Small legal and financial translation company needs Squarespace website, brochure and logo

Hello,
We are Lumarin Services (www.lumarinservices-example.com), a boutique legal and financial translation company. We offer our services mainly to Spanish customers. Our primary line of business is the translation of financial statements, but we translate a wide variety legal and financial texts.
The project we are offering comprises three parts: a redo of the current website, an informational brochure for potential customer and a logo design. These three parts should provide a consistent image. We would develop content soon.
We are looking for a website that would look like a typical law firm website, nothing too fancy. Right now, it is in English, Spanish and French, although the new site need only be in English and Spanish. There must be good toggling between the English and Spanish versions. There would be no need for tie-ins to social media and it would not contain a blog. Basically, a static site. We aren't interesting in driving traffic to the site or SEO, as we will contact nearly all potential customers beforehand. The website must be built in Squarespace to enable a smooth transition. The content would be similar to the current page, we'll be working on the exact content, but a rough draft is attached.
The brochure will be some three pages and would introduce the company to potential customers, using similar images as the website and the logo to be designed.
The only specifications for the logo is, as the website and brochure, it convey a sense of security and trust.
Feel free to ask with any questions as this is the first time we have used this platform.
Thank you!
Updates

I've added a more or less final version for the text in the brochure and updated the brief. Added Wednesday, June 10, 2015

Target Market(s)

Spanish law firms, auditors, accountants, banks, investment firms

Industry/Entity Type

Finance

Logo Text

Lumarin Services

Number of Pages Required

5+ page

Font styles to use
Serif

Requirements
Must have
• The website must be built in Squarespace and have a good option to toggle between English and Spanish versions.
• Brochure must be in both English and Spanish, I'm attaching a rough draft of the information that it will probably have. This should give an idea about what to include and the spacing. I will update it to include the final information.
Nice to have
• Would be nice to have some quality finance- and legal-related images
Should not have
• Vibrant colours

```html
<!DOCTYPE html>
<html lang="en">
<head>
<meta charset="utf-8">
<title>Benefits – Lumarin Services</title>
<link rel="stylesheet" href="https://fonts.googleapis.com/css2?family=EB+Garamond:wght@400;600;700&family=Montserrat:wght@500;600;800&display=swap">
<style>
  :root {
    --teal: #3aa3a3;
    --teal-dark: #2f8a87;
    --brand: #a9dcea;
    --page: #ececec;
    --ink: #3a3a3a;
    --ink-strong: #222;
    --muted: #9a9a9a;
    --footer-top: #333333;
    --footer-bottom: #1e1e1e;
    --white: #ffffff;
  }
  * { box-sizing: border-box; margin: 0; padding: 0; }
  html, body { width: 1200px; height: 1103px; overflow: hidden; }
  body { background: var(--page); font-family: "EB Garamond", Georgia, serif; color: var(--ink); position: relative; }

  .hero { position: absolute; left: 0; top: 0; width: 1200px; height: 444px; overflow: hidden; }
  .hero-photo { position: absolute; inset: 0; background:
      linear-gradient(100deg, #1f1f1f 0%, #3c3c3c 22%, #555 40%, #4a4a4a 55%, #6c6c6c 72%, #9a9a9a 82%, #3a3a3a 92%, #2a2a2a 100%); }
  .brand { position: absolute; left: 16px; top: 30px; font-family: "EB Garamond", Georgia, serif; font-size: 34px; line-height: 1; color: var(--brand); font-weight: 400; }
  .main-nav { position: absolute; right: 32px; top: 53px; display: flex; gap: 27px; }
  .main-nav a { font-family: "Montserrat", Arial, sans-serif; font-weight: 600; font-size: 11.5px; letter-spacing: 1.6px; color: var(--white); text-decoration: none; }
  .hero-title { position: absolute; left: 0; right: 0; top: 198px; text-align: center; font-family: "Montserrat", Arial, sans-serif; font-weight: 800; font-size: 55px; letter-spacing: 3px; color: var(--white); }

  .side-nav { position: absolute; left: 182px; top: 530px; width: 180px; }
  .side-nav h2 { font-weight: 400; font-size: 21px; color: var(--teal-dark); margin-bottom: 6px; }
  .side-nav a { display: block; font-family: "Montserrat", Arial, sans-serif; font-weight: 500; font-size: 12px; letter-spacing: 2px; line-height: 15px; color: var(--muted); text-decoration: none; margin-bottom: 9px; text-transform: uppercase; }
  .side-nav a.current { color: var(--ink-strong); }

  .content { position: absolute; left: 408px; top: 530px; width: 600px; }
  .content h1 { font-weight: 400; font-size: 38px; color: var(--teal); margin-bottom: 20px; letter-spacing: 0.2px; }
  .benefits { list-style: none; }
  .benefits li { position: relative; padding-left: 68px; font-size: 17.5px; line-height: 23px; letter-spacing: 1.1px; width: 584px; margin-bottom: 9px; }
  .benefits li.bulleted::before { content: ""; position: absolute; left: 18px; top: 10px; width: 5px; height: 5px; border-radius: 50%; background: var(--ink); }
  .benefits strong { font-weight: 700; color: var(--ink-strong); }

  .footer-top { position: absolute; left: 0; top: 984px; width: 1200px; height: 56px; background: var(--footer-top); }
  .footer-bottom { position: absolute; left: 0; top: 1040px; width: 1200px; height: 63px; background: var(--footer-bottom); }
</style>
</head>
<body>
  <header class="hero">
    <div class="hero-photo" role="img" aria-label="Black and white photograph looking up at glass office towers"></div>
    <div class="brand">Lumarin Services</div>
    <nav class="main-nav">
      <a href="#">HOME</a>
      <a href="#">ENGLISH</a>
      <a href="#">SPANISH</a>
    </nav>
    <div class="hero-title">BENEFITS</div>
  </header>

  <aside class="side-nav">
    <h2>English</h2>
    <a href="#">Who we are</a>
    <a href="#" class="current">Benefits</a>
    <a href="#">Legal translation</a>
    <a href="#">Financial translation</a>
    <a href="#">Contact</a>
  </aside>

  <main class="content">
    <h1>Benefits of working with us:</h1>
    <ul class="benefits">
      <li class="bulleted">Translations entrusted to a specialist company save both <strong>time and money</strong></li>
      <li class="bulleted"><strong>Guaranteed quality</strong> time and time again</li>
      <li>Promise that expert translators work only in their mother tongue</li>
      <li>A <strong>consistent voice</strong> cultivated over time and across channels ensures that your <strong>firm speaks with one voice</strong></li>
      <li>Use of cutting-edge technology helps cut costs by ensuring <strong>competitive budgets</strong> based on past work</li>
    </ul>
  </main>

  <footer>
    <div class="footer-top"></div>
    <div class="footer-bottom"></div>
  </footer>
</body>
</html>
```